Card Design for my dog training business Brightpaw Obedience

Need a business card design for my dog training business with my new logo. Want the card to come off professional yet fun. Want it to be very eye catchy as well. I normally have these at vet clinics, pet stores, and groomers. so need it to look better than my competitors.
Target Market(s)
dog owners
Industry/Entity Type
Dog Training
Contact Information for Business Card
needs logo, my name and info
Font styles to use
Serif
Colors
0255a3
ffffff
ec1f27
000000
333333
fbfbfb
Requirements
Must have
- Brightpaw Obedience
- Felix Orland
- 415 903 2276
- info@brightpawobedience.example
- www.brightpawobedience.example

```html
<!DOCTYPE html>
<html lang="en">
<head>
<meta charset="utf-8">
<title>Brightpaw Obedience – Business Card</title>
<link rel="stylesheet" href="https://fonts.googleapis.com/css2?family=Noto+Serif:wght@400&family=EB+Garamond:ital@1&display=swap">
<style>
  :root {
    --blue: #0255a3;
    --white: #ffffff;
    --red: #ec1f27;
    --black: #000000;
    --ink: #333333;
    --paper: #fbfbfb;
    --backdrop: #b9b9b9;
  }
  * { margin: 0; padding: 0; box-sizing: border-box; }
  html, body { width: 1200px; height: 576px; overflow: hidden; }
  body {
    background: var(--backdrop);
    position: relative;
    font-family: "Noto Serif", Georgia, serif;
  }
  .card {
    position: absolute;
    top: 138px;
    height: 294px;
    border-radius: 12px;
    overflow: hidden;
    background: linear-gradient(180deg, var(--paper), #ececec);
    box-shadow: 0 3px 6px rgba(0,0,0,.25);
  }
  .card--back { left: 81px; width: 485px; }
  .card--front { left: 602px; width: 480px; }

  .brand {
    position: absolute;
    display: flex;
    flex-direction: column;
    align-items: center;
    gap: 12px;
  }
  .brand__dot {
    width: 46px; height: 46px; border-radius: 50%;
  }
  .brand__name {
    font-size: 19px;
    letter-spacing: .5px;
    white-space: nowrap;
  }
  .card--back .brand { left: 0; right: 0; top: 92px; }
  .card--back .brand__dot { background: var(--ink); }
  .card--back .brand__name { color: var(--ink); }
  .card--front .brand { left: 0; width: 200px; top: 96px; }
  .card--front .brand__dot { background: var(--blue); }
  .card--front .brand__name { color: var(--blue); font-size: 16px; }

  .tagline-band {
    position: absolute;
    left: 0; right: 0; top: 256px; height: 28px;
    background: var(--blue);
    color: var(--white);
    font-family: "EB Garamond", Georgia, serif;
    font-style: italic;
    font-size: 12.5px;
    display: flex; align-items: center; justify-content: center;
  }

  .front-panel { position: absolute; inset: 0; }

  .holder {
    position: absolute;
    right: 24px; top: 40px;
    text-align: right;
    color: var(--white);
  }
  .holder__name { font-size: 21px; line-height: 1.2; }
  .holder__role { font-size: 12.5px; margin-top: 2px; }

  .contact {
    position: absolute;
    right: 24px; top: 206px;
    list-style: none;
    color: var(--white);
    font-size: 11.5px;
  }
  .contact__item {
    display: flex; align-items: center; justify-content: flex-end;
    gap: 10px; height: 19.5px;
    white-space: nowrap;
  }
  .contact__icon { width: 11px; height: 11px; fill: var(--white); flex: none; }
</style>
</head>
<body>

  <section class="card card--back" aria-label="Card back">
    <div class="brand">
      <span class="brand__dot"></span>
      <span class="brand__name">Brightpaw Obedience</span>
    </div>
    <p class="tagline-band">“Teaching good manners one happy dog at a time.”</p>
  </section>

  <section class="card card--front" aria-label="Card front">
    <svg class="front-panel" width="480" height="294" viewBox="0 0 480 294">
      <path d="M199 0 Q277 147 194 294 L480 294 L480 0 Z" fill="var(--red)"/>
      <path d="M199 0 Q283 147 203 294 L480 294 L480 0 Z" fill="var(--blue)"/>
      <circle cx="482" cy="86" r="13" fill="var(--red)"/>
    </svg>

    <div class="brand">
      <span class="brand__dot"></span>
      <span class="brand__name">Brightpaw Obedience</span>
    </div>

    <div class="holder">
      <p class="holder__name">Felix Orland</p>
      <p class="holder__role">Dog Trainer</p>
    </div>

    <ul class="contact">
      <li class="contact__item">415 903 2276
        <svg class="contact__icon" viewBox="0 0 12 12"><path d="M1 4 Q6 0 11 4 L10 5.5 L8 4.8 L8 4 Q6 3 4 4 L4 4.8 L2 5.5 Z M3 6 H9 L10 11 H2 Z"/></svg>
      </li>
      <li class="contact__item">info@brightpawobedience.example
        <svg class="contact__icon" viewBox="0 0 12 12"><path d="M1 2.5 H11 V9.5 H1 Z M1.8 3.2 L6 6.5 L10.2 3.2" fill="none" stroke="var(--white)" stroke-width="1.2"/></svg>
      </li>
      <li class="contact__item">www.brightpawobedience.example
        <svg class="contact__icon" viewBox="0 0 12 12"><g fill="none" stroke="var(--white)" stroke-width="1"><circle cx="6" cy="6" r="5"/><ellipse cx="6" cy="6" rx="2.2" ry="5"/><path d="M1 6 H11"/></g></svg>
      </li>
    </ul>
  </section>

</body>
</html>
```